Business Card Design

I am a realtor and i also flip houses. I am CEO and Founder of my business which is Voskell Group LLC which is named after my great uncle who died and i was really close to. He was a wonderful friendly man so i want my business to represent him too. My business works with a lot of different people but i want mainly something to show i am a strong confidant woman who owns there own business. I have a really fun personality so i don't want anything TOO serious or manly. I want the perfect mix. My last two business cards i created are too embarrassing to hand out because they are far too girly and i deal with a lot of millionaire clients. I live out in the Palm Springs California area. I think its very important to show i am a single mom, female with her own business at only 24. I don't want to just be a female that blends in with all of the other serious people but yet i don't want to seem immature. People are telling me to stay away from pinks and purples but i don't want blues and greens because they represent men more. But i won't say no to them if there is a happy medium.

Industry/Entity Type

Realtor

Contact Information for Business Card

Voskell Group, LLC
Corinne Tabb
27358 Halvern Ave, C2 517
Sable Springs, NV 89417
760-419-6735
Corinnedtabb@mailvane.com

```html
<!DOCTYPE html>
<html lang="en">
<head>
<meta charset="utf-8">
<title>Voskell Group LLC – Business Card</title>
<link href="https://fonts.googleapis.com/css2?family=Nova+Square&display=swap" rel="stylesheet">
<style>
  :root {
    --blush: #f2b1d6;
    --dusk: #9aa2b6;
    --lagoon: #4a8f9a;
    --teal: #338a93;
    --lemon: #f6f37c;
    --card-w: 1200px;
    --card-h: 702px;
  }
  html, body {
    margin: 0;
    padding: 0;
    width: var(--card-w);
    height: var(--card-h);
    overflow: hidden;
    background: #ffffff;
  }
  .business-card {
    position: relative;
    width: var(--card-w);
    height: var(--card-h);
    background: linear-gradient(90deg,
      var(--blush) 0%,
      var(--dusk) 12%,
      var(--lagoon) 27%,
      var(--teal) 40%,
      var(--teal) 100%);
    font-family: "Nova Square", "Arial", sans-serif;
    color: var(--lemon);
    overflow: hidden;
  }
  .line {
    position: absolute;
    margin: 0;
    white-space: nowrap;
    line-height: 1;
    transform: translateY(-50%);
    font-weight: 400;
  }
  .company-name {
    left: 67px;
    top: 354px;
    font-size: 51px;
    letter-spacing: 1px;
  }
  .agent-name {
    left: 646px;
    top: 238px;
    font-size: 57px;
    letter-spacing: 1.5px;
  }
  .address-line {
    left: 647px;
    font-size: 37px;
  }
  .address-street { top: 320px; }
  .address-unit   { top: 384px; }
  .address-state  { top: 446px; }
  .contact-icon {
    position: absolute;
    transform: translateY(-50%);
    fill: var(--lemon);
  }
  .icon-phone { left: 316px; top: 565px; width: 46px; height: 46px; }
  .icon-mail  { left: 313px; top: 630px; width: 50px; height: 38px; }
  .contact-phone {
    left: 391px;
    top: 559px;
    font-size: 36px;
    letter-spacing: 1px;
  }
  .contact-email {
    left: 403px;
    top: 626px;
    font-size: 35px;
    letter-spacing: 0.5px;
  }
</style>
</head>
<body>
  <main class="business-card">
    <p class="line company-name">Voskell Group LLC</p>

    <h1 class="line agent-name">Corinne Tabb</h1>
    <p class="line address-line address-street">27358 Halvern Ave</p>
    <p class="line address-line address-unit">C2 517 Sable Springs</p>
    <p class="line address-line address-state">NV 89417</p>

    <svg class="contact-icon icon-phone" viewBox="0 0 24 24" aria-hidden="true">
      <path d="M6.6 10.8c1.4 2.8 3.8 5.1 6.6 6.6l2.2-2.2c.3-.3.7-.4 1-.2 1.1.4 2.3.6 3.6.6.6 0 1 .4 1 1V20c0 .6-.4 1-1 1C10.6 21 3 13.4 3 4c0-.6.4-1 1-1h3.5c.6 0 1 .4 1 1 0 1.3.2 2.5.6 3.6.1.3 0 .7-.2 1l-2.3 2.2z"/>
    </svg>
    <p class="line contact-phone">760-419-6735</p>

    <svg class="contact-icon icon-mail" viewBox="0 0 50 38" aria-hidden="true">
      <path d="M0 0h50v38H0z M4 4v1.5l21 16 21-16V4z M4 10.5V34h42V10.5L25 26.5z" fill-rule="evenodd"/>
    </svg>
    <p class="line contact-email">corinnedtabb@mailvane.com</p>
  </main>
</body>
</html>
```